Veldmark Supplies Business Card

Professional business card that stand out to our potential customers. Front and back with clean modern design

Industry/Entity Type

Oil and gas

Contact Information for Business Card

Name, address, website , office phone and cell number

Requirements
Must have
• Editable files for each employee

```html
<!DOCTYPE html>
<html lang="en">
<head>
<meta charset="utf-8">
<title>Veldmark Supplies Business Card</title>
<link rel="stylesheet" href="https://fonts.googleapis.com/css2?family=Roboto:wght@400;500;700;900&display=swap">
<style>
  :root {
    --bg: #2b2b2d;
    --card: #232427;
    --card-edge: #1b1c1e;
    --red: #e01b24;
    --blue: #29a9d6;
    --white: #f4f4f4;
    --muted: #d6d6d6;
  }
  * { box-sizing: border-box; margin: 0; padding: 0; }
  html, body { width: 1200px; height: 852px; overflow: hidden; }
  body {
    background: var(--bg);
    font-family: "Roboto", Arial, sans-serif;
    position: relative;
  }
  .card {
    position: absolute;
    width: 520px;
    height: 297px;
    border-radius: 26px;
    background: var(--card);
    overflow: hidden;
    box-shadow: 0 14px 30px rgba(0,0,0,.45);
  }
  .card-back { left: 70px; top: 110px; }
  .card-front { left: 610px; top: 445px; }

  /* back side */
  .back-brand {
    position: absolute;
    left: 0; right: 0; top: 0; bottom: 0;
    display: flex;
    align-items: center;
    justify-content: center;
    gap: 16px;
  }
  .back-brand .brand-mark {
    width: 26px; height: 26px;
    background: var(--red);
  }
  .back-brand .brand-name {
    font-weight: 900;
    font-size: 34px;
    letter-spacing: 1px;
    text-transform: uppercase;
    color: var(--white);
  }

  /* front side */
  .front-shape { position: absolute; left: 0; top: 0; }
  .front-brand {
    position: absolute;
    left: 0; top: 0;
    width: 235px; height: 297px;
    display: flex;
    flex-direction: column;
    align-items: center;
    justify-content: center;
    gap: 12px;
  }
  .front-brand .brand-mark {
    width: 22px; height: 22px;
    background: var(--white);
  }
  .front-brand .brand-name {
    font-weight: 900;
    font-size: 22px;
    line-height: 1.15;
    text-align: center;
    text-transform: uppercase;
    color: var(--white);
  }
  .contact {
    position: absolute;
    left: 300px; top: 44px;
    color: var(--muted);
    font-size: 12.5px;
    line-height: 1.4;
  }
  .contact .person-name {
    color: var(--blue);
    font-weight: 700;
    font-size: 19px;
    line-height: 1.1;
  }
  .contact .person-role { color: var(--white); font-size: 12px; margin-bottom: 22px; }
  .contact .address { margin-bottom: 12px; }
  .contact-line { display: flex; align-items: center; gap: 8px; }
  .contact-line svg { width: 11px; height: 11px; flex: none; }
</style>
</head>
<body>

<section class="card card-back" aria-label="Card back">
  <div class="back-brand">
    <span class="brand-mark"></span>
    <span class="brand-name">Veldmark Supplies</span>
  </div>
</section>

<section class="card card-front" aria-label="Card front">
  <svg class="front-shape" width="520" height="297" viewBox="0 0 520 297" aria-hidden="true">
    <path d="M0 0 H150 Q270 60 300 297 H0 Z" fill="var(--blue)"/>
    <path d="M0 0 H140 Q255 62 284 297 H0 Z" fill="var(--red)"/>
  </svg>
  <div class="front-brand">
    <span class="brand-mark"></span>
    <span class="brand-name">Veldmark<br>Supplies</span>
  </div>

  <div class="contact">
    <p class="person-name">Alan Reed Carter</p>
    <p class="person-role">Managing Director</p>
    <p class="address">412 Mesa Ridge Suite 3<br>Larkton, Tx 79000</p>
    <p class="contact-line">
      <svg viewBox="0 0 12 12" aria-hidden="true"><path d="M2 1 L4 1 L5 4 L3.8 5 Q5 7.5 7 8.2 L8 7 L11 8 L11 10 Q10 11.5 8 11 Q2 9 1 3 Q1 1.2 2 1 Z" fill="var(--red)"/></svg>
      (555)610-0148
    </p>
    <p class="contact-line">
      <svg viewBox="0 0 12 12" aria-hidden="true"><rect x="1" y="2.5" width="10" height="7" rx="1" fill="var(--red)"/><path d="M1.5 3 L6 6.5 L10.5 3" stroke="var(--card)" stroke-width="1" fill="none"/></svg>
      sales@veldmarksupplies.com
    </p>
    <p class="contact-line">
      <svg viewBox="0 0 12 12" aria-hidden="true"><circle cx="6" cy="6" r="5" fill="var(--red)"/><path d="M1 6 H11 M6 1 V11 M6 1 Q3 6 6 11 M6 1 Q9 6 6 11" stroke="var(--card)" stroke-width=".8" fill="none"/></svg>
      www.veldmarksupplies.com
    </p>
  </div>
</section>

</body>
</html>
```